Building company needs a letterhead design

I'm after a modern but professional letter head.
Must have the below details:
- Logo
- Website - TARVELLGROUP.COM.AU
- Email - INFO@TARVELLGROUP.COM.AU
- Office - 03 57263018
- Mobile number - 0418536294
- ABN - 47 315 962 108
...........................................................................................................................................................................................................................
- Logo
- Office - 03 57263018
- ABN - 47 315 962 108

Target Market(s)

.

Industry/Entity Type

Construction Company

Font styles to use
Sans Serif

Requirements
Must have
• Must have the below details:
• - Logo
• - Website - TARVELLGROUP.COM.AU
• - Email - INFO@TARVELLGROUP.COM.AU
• - Office - 03 57263018
• - Mobile number - 0418536294
• - ABN - 47 315 962 108
Nice to have
• .
Should not have
• .

```html
<!DOCTYPE html>
<html lang="en">
<head>
<meta charset="utf-8">
<title>Tarvell Building Group — Letterhead</title>
<link href="https://fonts.googleapis.com/css2?family=Open+Sans:wght@400;600;700&display=swap" rel="stylesheet">
<style>
  :root {
    --backdrop: #e6e6e6;
    --paper: #ffffff;
    --brand-yellow: #e9a800;
    --brand-charcoal: #4a4a4a;
    --text-dark: #1a1a1a;
    --text-muted: #4d4d4d;
  }
  * { box-sizing: border-box; margin: 0; padding: 0; }
  html, body {
    width: 1200px; height: 1192px; overflow: hidden;
    background: var(--backdrop);
    font-family: "Open Sans", Arial, sans-serif;
  }
  .letterhead {
    position: absolute; left: 220px; top: 58px;
    width: 760px; height: 1075px;
    background: var(--paper);
    box-shadow: 0 2px 10px rgba(0,0,0,0.08);
    overflow: hidden;
  }
  .header-swoosh { position: absolute; left: 0; top: 0; width: 760px; height: 200px; }
  .brand-name {
    position: absolute; right: 56px; top: 178px;
    text-align: right; color: var(--brand-yellow);
    font-weight: 700; line-height: 1.05;
  }
  .brand-name .brand-primary { display: block; font-size: 30px; letter-spacing: 2px; }
  .brand-name .brand-secondary { display: block; font-size: 12px; letter-spacing: 2.6px; }
  .contact-list {
    position: absolute; left: 60px; bottom: 120px;
    list-style: none; font-size: 13px; color: var(--text-muted); line-height: 20px;
  }
  .contact-list li { display: flex; align-items: center; gap: 10px; }
  .contact-list svg { width: 11px; height: 11px; fill: var(--brand-yellow); flex: none; }
  .contact-list .no-icon { padding-left: 21px; }
  .abn {
    position: absolute; right: 90px; bottom: 80px;
    font-size: 13px; font-weight: 700; color: var(--text-dark);
  }
</style>
</head>
<body>
  <main class="letterhead">
    <svg class="header-swoosh" viewBox="0 0 760 200" aria-hidden="true">
      <path d="M0 0 H420 Q180 40 0 125 Z" fill="var(--brand-yellow)"/>
      <path d="M0 150 Q190 55 430 10 Q200 60 0 136 Z" fill="var(--brand-charcoal)"/>
    </svg>

    <div class="brand-name">
      <span class="brand-primary">TARVELL</span>
      <span class="brand-secondary">BUILDING GROUP</span>
    </div>

    <ul class="contact-list">
      <li>
        <svg viewBox="0 0 12 12"><path d="M2.5 0.5l2 2.5-1.2 1.2c.7 1.6 2 2.9 3.5 3.5l1.2-1.2 2.5 2-1 2C6 10.7 1.3 6 0.5 2.5z"/></svg>
        03 57263018
      </li>
      <li>
        <svg viewBox="0 0 12 12"><path d="M3 0h6a1 1 0 0 1 1 1v10a1 1 0 0 1-1 1H3a1 1 0 0 1-1-1V1a1 1 0 0 1 1-1zm0 1.5v8h6v-8z"/></svg>
        0418536294
      </li>
      <li>
        <svg viewBox="0 0 12 12"><path d="M0 2h12v8H0zm1 1v.4l5 3.3 5-3.3V3z"/></svg>
        info@tarvellgroup.com.au
      </li>
      <li>
        <svg viewBox="0 0 12 12"><path d="M6 0a6 6 0 1 0 0 12A6 6 0 0 0 6 0zm0 1.5a4.5 4.5 0 1 1 0 9 4.5 4.5 0 0 1 0-9z"/></svg>
        www.tarvellgroup.com.au
      </li>
    </ul>

    <p class="abn">ABN - 47 315 962 108</p>
  </main>
</body>
</html>
```